Sports Event - Web Design Project

We run an event called GRIT & GLORY which is "Ireland's Wildest 10K Ordeal" - so running through water, covered in mud, through electric fences etc. Similar type event to GrimSlogger or Vorlaxian Dash internationally

Have 2,500 people signed up for next event in January so want to revamp our current website www.gritandglory.ie and bring it up to the next level.

We are looking for 3 pages to be deisgned: a template site page, a Home Page & an Events Page with interactive map. I have already made a "home made" design of what we want - so this design will give you a good idea of the style and colours we want...then its up to you to add your skill and personality to make the new website exciting, stylish and professional.
Updates

I have just posted a web page which gives a bit more detail about the 3 pages we are looking for, the style etc

we have our own web developers who will take your design and implement it into the back end of our customised website...so whoever gets the job, I will get them to speak with our developer about what is the best way to give the final artwork etc to us. 

Here is the webpage with our "Homemade" designs on it to give you an idea of all the things we are looking for

http://www.brambleroute.ie/News/New-Website-Screenshots-post-35.htm

Here is the GRIT & GLORY logo - sorry dont know how else up to upload it

For the Interactive Map (Event Page), go to the following link for actual course:

Target Market(s)

Male and female, sporty and non-sporty (lots of people do this event for charity). Aged 21-45. People looking for a fun challenge

Industry/Entity Type

Events

Requirements
Must have
• Require 3 pages:
1. Home Page (with video being central point)
2. Events Page with interactive map
3. Template Site Page

See this link for more info:

We also require each of these designs to be enabled in the following formats:
1. PC / Desktop
2. iPad / Tablet
3. Phone

Must use the orange, red and black of GRIT & GLORY logo, as well as some type of hellish fire/flames

```html
<!DOCTYPE html>
<html lang="en">
<head>
<meta charset="utf-8">
<title>GRIT &amp; GLORY – Ireland's Wildest 10K Ordeal</title>
<link rel="stylesheet" href="https://fonts.googleapis.com/css2?family=Black+Ops+One&family=Ubuntu:wght@400;500;700&family=Dancing+Script:wght@600&display=swap">
<style>
:root{
  --fire-deep:#b8300a;
  --fire-red:#e0440c;
  --fire-mid:#f07a12;
  --fire-bright:#ffc629;
  --fire-glow:#fff2a0;
  --band-orange:#f3892a;
  --red:#d7262c;
  --yellow:#fff22a;
  --cyan:#1ccfd8;
  --green:#6de07a;
  --ink:#141210;
  --cream:#fff7c8;
  --footer:#2a2520;
  --white:#ffffff;
}
*{box-sizing:border-box;margin:0;padding:0}
html,body{width:1200px;height:1175px;overflow:hidden}
body{
  position:relative;
  font-family:"Ubuntu",sans-serif;
  background:linear-gradient(180deg, var(--fire-deep) 0%, var(--fire-mid) 22%, var(--fire-bright) 62%, #ffd750 100%);
}
.abs{position:absolute}

/* flame backdrop: tall soft tongues of colour */
.fire-bg{
  position:absolute;inset:0;
  background:
    radial-gradient(ellipse 26px 210px at 40px 330px, rgba(255,244,170,.9), transparent 70%),
    radial-gradient(ellipse 30px 260px at 95px 520px, rgba(255,250,190,.85), transparent 70%),
    radial-gradient(ellipse 24px 200px at 20px 720px, rgba(255,240,150,.85), transparent 70%),
    radial-gradient(ellipse 34px 240px at 80px 900px, rgba(255,250,200,.8), transparent 70%),
    radial-gradient(ellipse 22px 180px at 115px 300px, rgba(200,40,8,.55), transparent 70%),
    radial-gradient(ellipse 20px 220px at 60px 640px, rgba(210,60,10,.5), transparent 70%),
    radial-gradient(ellipse 26px 210px at 1100px 330px, rgba(255,244,170,.9), transparent 70%),
    radial-gradient(ellipse 30px 260px at 1160px 540px, rgba(255,250,190,.85), transparent 70%),
    radial-gradient(ellipse 24px 220px at 1095px 760px, rgba(255,240,150,.85), transparent 70%),
    radial-gradient(ellipse 32px 230px at 1170px 930px, rgba(255,250,200,.8), transparent 70%),
    radial-gradient(ellipse 22px 200px at 1135px 420px, rgba(200,40,8,.55), transparent 70%),
    radial-gradient(ellipse 22px 210px at 1185px 700px, rgba(210,60,10,.5), transparent 70%),
    radial-gradient(ellipse 20px 34px at 90px 18px, rgba(255,230,120,.9), transparent 75%),
    radial-gradient(ellipse 22px 36px at 260px 20px, rgba(255,220,100,.85), transparent 75%),
    radial-gradient(ellipse 18px 34px at 430px 18px, rgba(255,235,130,.9), transparent 75%),
    radial-gradient(ellipse 24px 36px at 610px 20px, rgba(255,225,110,.85), transparent 75%),
    radial-gradient(ellipse 20px 34px at 790px 18px, rgba(255,235,130,.9), transparent 75%),
    radial-gradient(ellipse 22px 36px at 960px 20px, rgba(255,220,100,.85), transparent 75%),
    radial-gradient(ellipse 20px 34px at 1130px 18px, rgba(255,235,130,.9), transparent 75%),
    radial-gradient(ellipse 40px 120px at 600px 1000px, rgba(255,250,200,.6), transparent 70%),
    radial-gradient(ellipse 60px 60px at 600px 840px, rgba(255,250,190,.7), transparent 70%),
    repeating-linear-gradient(90deg, rgba(190,40,6,.18) 0 14px, rgba(255,230,120,.14) 14px 38px, rgba(220,80,10,.12) 38px 55px, rgba(255,245,170,.12) 55px 80px);
}

/* header */
.header-band{left:0;top:38px;width:1200px;height:150px;background:var(--band-orange);box-shadow:0 3px 6px rgba(0,0,0,.25)}
.brand{left:92px;top:20px;width:270px;height:236px;display:flex;align-items:center;justify-content:center;gap:10px}
.brand-mark{width:30px;height:30px;border-radius:50%;background:var(--red);flex:none}
.brand-name{font-family:"Black Ops One",sans-serif;font-size:30px;color:var(--red);line-height:1}
.nav{left:380px;top:78px;display:flex;gap:8px}
.nav a{width:92px;height:72px;display:flex;align-items:center;justify-content:center;text-align:center;
  font-family:"Black Ops One",sans-serif;font-size:16px;line-height:1.15;text-decoration:none;color:var(--white);letter-spacing:.5px}
.nav .red{background:var(--red)}
.nav .yellow{background:var(--yellow);color:#4a3b10}
.nav .cyan{background:var(--cyan);color:#184a4e}
.nav .green{background:var(--green);color:#1f4a22}

/* video */
.video{left:133px;top:213px;width:695px;height:399px;background:var(--white);padding:3px}
.video-frame{position:relative;width:100%;height:100%;background:linear-gradient(160deg,#4c5a3c,#2b2d24 55%,#1a1b16)}
.play{left:305px;top:143px;width:84px;height:84px}
.caption{left:22px;top:296px;font-family:"Dancing Script",cursive;font-size:30px;color:rgba(255,255,255,.75)}
.controls{left:0;bottom:0;width:100%;height:32px;background:#1b1b1b;color:#ccc;font-size:11px}
.progress{left:0;top:0;width:100%;height:3px;background:#555}
.progress span{display:block;width:45%;height:100%;background:#c40000}
.time{left:100px;top:11px}

/* side */
.signup{left:851px;top:213px;width:218px;height:175px;background:var(--red);border:3px solid var(--white)}
.signup-inner{left:18px;top:22px;width:180px;height:110px;background:var(--fire-bright);transform:rotate(-7deg);
  display:flex;flex-direction:column;align-items:center;justify-content:center;font-family:"Black Ops One",sans-serif;color:var(--ink)}
.signup-inner .s1{font-size:28px}
.signup-inner .s2{font-size:46px;line-height:1}
.devils{left:851px;top:404px;width:218px;height:211px;background:var(--yellow);border:3px solid var(--white)}
.devils h3{position:absolute;left:16px;top:16px;font-family:"Black Ops One",sans-serif;font-size:21px;font-weight:400;color:#3a2a08}
.email{left:16px;top:49px;width:183px;height:31px;background:#222;border:1px solid #555;color:#aaa;font-size:14px;font-style:italic;padding:6px 12px}
.join{left:149px;top:90px;width:50px;height:30px;background:var(--red);color:var(--white);font-family:"Black Ops One",sans-serif;font-size:16px;display:flex;align-items:center;justify-content:center}
.follow{left:16px;top:132px;font-size:14px;color:#333}
.socials{left:20px;top:158px;display:flex;gap:5px}
.socials span{width:30px;height:30px;border-radius:4px}

/* events */
.events-bar{left:131px;top:637px;width:699px;height:41px;background:var(--band-orange);box-shadow:0 2px 4px rgba(0,0,0,.2)}
.events-bar h2{position:absolute;left:48px;top:8px;font-family:"Black Ops One",sans-serif;font-weight:400;font-size:20px;color:var(--ink)}
.cal{left:10px;top:6px}
.cards{left:131px;top:691px;display:flex;gap:8px}
.card{position:relative;width:169px;height:145px;border:2px solid var(--white);border-radius:6px;overflow:hidden;background:var(--ink)}
.card-title{height:26px;display:flex;align-items:center;justify-content:center;color:var(--yellow);font-weight:700;font-size:19px}
.card-photo{height:88px;background:linear-gradient(160deg,#6d6e5e,#3b3a30)}
.card-date{height:29px;display:flex;align-items:center;justify-content:center;color:var(--white);font-size:17px}

.charity{left:849px;top:636px;width:220px;height:181px;background:var(--white);border-radius:6px;overflow:hidden;box-shadow:0 2px 5px rgba(0,0,0,.3)}
.charity-name{left:14px;top:8px;font-size:24px;color:#2b6e1f}
.charity-copy{left:15px;top:44px;font-size:14px;color:#333;line-height:1.6}
.charity-copy b{color:var(--red);font-weight:400;font-size:18px;line-height:1.3}
.charity-art{left:112px;top:70px;width:100px;height:82px;border-radius:8px;background:linear-gradient(160deg,#d9e8d0,#3aa04a)}
.charity-foot{left:0;bottom:0;width:100%;height:31px;background:#4a4a4a;color:var(--white);font-size:14px;font-weight:500;padding:7px 14px}

/* partners */
.partners{left:131px;top:858px;width:938px;height:157px;background:rgba(255,236,150,.8);border-radius:3px;overflow:hidden}
.partners-glow{inset:0;background:
  radial-gradient(ellipse 50px 80px at 680px 120px, rgba(255,190,60,.45), transparent 70%),
  radial-gradient(ellipse 70px 60px at 860px 140px, rgba(255,170,40,.4), transparent 70%),
  radial-gradient(ellipse 60px 50px at 120px 150px, rgba(255,200,70,.35), transparent 70%)}
.partners h2{position:absolute;left:18px;top:17px;font-family:"Black Ops One",sans-serif;font-weight:400;font-size:20px;color:var(--ink)}
.arrow{top:60px}
.logos{left:70px;top:66px;width:800px;display:flex;justify-content:space-around;align-items:center;font-size:30px;font-weight:700;color:#2b2b2b}

/* footer */
.footer{left:131px;top:1035px;width:938px;height:115px;background:var(--footer);border-radius:6px}
.footer-links{left:16px;top:39px;font-size:11.5px;color:#e5e5e5;word-spacing:1px}
.copy{left:16px;top:61px;font-size:12px;color:#e5e5e5;display:flex;align-items:center;gap:6px}
.copy em{font-style:normal;color:var(--fire-bright)}
.tc{background:var(--yellow);color:#333;padding:3px 9px;border-radius:3px;font-size:11px}
.by{left:675px;top:6px;width:257px;height:104px;background:var(--yellow);border:3px solid var(--white);border-radius:4px;text-align:center}
.by h4{font-family:"Black Ops One",sans-serif;font-weight:400;font-size:18px;color:#333;margin-top:6px}
.by .partner{margin-top:20px;font-size:22px;font-weight:700;color:var(--ink)}
.by .tag{font-size:11px;color:var(--ink)}
</style>
</head>
<body>
<div class="fire-bg" role="img" aria-label="Background of roaring orange, red and yellow flames"></div>

<header>
  <div class="abs header-band"></div>
  <div class="abs brand"><span class="brand-mark"></span><span class="brand-name">GRIT &amp; GLORY</span></div>
  <nav class="abs nav">
    <a class="red" href="#">EVENTS</a>
    <a class="yellow" href="#">GET<br>INVOLVED</a>
    <a class="cyan" href="#">PHOTOS</a>
    <a class="green" href="#">VIDEOS</a>
    <a class="yellow" href="#">HALL OF<br>FAME</a>
    <a class="red" href="#">WHO WE<br>ARE</a>
    <a class="cyan" href="#">CONTACT<br>US</a>
  </nav>
</header>

<section class="abs video">
  <div class="video-frame" role="img" aria-label="Video still of muddy runners climbing through a forest trail">
    <svg class="abs play" viewBox="0 0 84 84"><circle cx="42" cy="42" r="42" fill="rgba(255,255,255,.8)"/><path d="M32 24 L62 42 L32 60 Z" fill="#1a1a1a"/></svg>
    <p class="abs caption">Listen! There is even a baby crying. Epic!</p>
    <div class="abs controls">
      <div class="abs progress"><span></span></div>
      <svg class="abs" style="left:22px;top:10px" width="60" height="14"><rect x="0" y="0" width="4" height="14" fill="#999"/><rect x="7" y="0" width="4" height="14" fill="#999"/><path d="M40 4h4l5-4v14l-5-4h-4z" fill="#999"/></svg>
      <span class="abs time"><b style="color:#ddd">1:56</b> / 4:17</span>
    </div>
  </div>
</section>

<aside>
  <div class="abs signup">
    <div class="abs signup-inner"><span class="s1">SIGN UP</span><span class="s2">NOW!</span></div>
  </div>
  <div class="abs devils">
    <h3>DEVILS UNITE</h3>
    <div class="abs email">Your E- Mail</div>
    <div class="abs join">JOIN</div>
    <p class="abs follow">Follow Us:</p>
    <div class="abs socials">
      <span style="background:#3b5bb0"></span>
      <span style="background:#5cc6ea"></span>
      <span style="background:#1673b6"></span>
      <span style="background:#d6251f"></span>
      <span style="background:#f28a17"></span>
    </div>
  </div>
</aside>

<section>
  <div class="abs events-bar">
    <svg class="abs cal" width="28" height="28" viewBox="0 0 28 28"><rect x="1" y="3" width="26" height="24" rx="3" fill="#fff" stroke="#c33" stroke-width="1.5"/><rect x="1" y="3" width="26" height="7" rx="3" fill="#d7262c"/><g fill="#bbb"><rect x="5" y="13" width="4" height="3"/><rect x="12" y="13" width="4" height="3"/><rect x="19" y="13" width="4" height="3"/><rect x="5" y="19" width="4" height="3"/><rect x="12" y="19" width="4" height="3"/></g></svg>
    <h2>UPCOMING EVENTS</h2>
  </div>
  <div class="abs cards">
    <article class="card"><div class="card-title">TROJAN</div><div class="card-photo" role="img" aria-label="Runners wading through a muddy stream"></div><div class="card-date">3rd Feb 2013</div></article>
    <article class="card"><div class="card-title">APOLLO</div><div class="card-photo" role="img" aria-label="Runner crawling under an electric fence"></div><div class="card-date">16th Feb 2013</div></article>
    <article class="card"><div class="card-title">TITAN</div><div class="card-photo" role="img" aria-label="Participants crawling through deep mud"></div><div class="card-date">23rd Oct 2013</div></article>
    <article class="card"><div class="card-title">ZEUS</div><div class="card-photo" role="img" aria-label="Group of mud-covered finishers celebrating"></div><div class="card-date">18th Jan 2014</div></article>
  </div>
  <div class="abs charity">
    <p class="abs charity-name">Kindpurse.ie</p>
    <p class="abs charity-copy">Provider of online<br><b>Fundrising</b><br>Services to<br><b>Charities</b></p>
    <div class="abs charity-art" role="img" aria-label="Hand dropping a coin into a green collection tin"></div>
    <p class="abs charity-foot">Helping you to help others</p>
  </div>
</section>

<section class="abs partners">
  <div class="abs partners-glow" role="img" aria-label="Faint flames rising across the partners panel"></div>
  <h2>OUR PARTNERS</h2>
  <svg class="abs arrow" style="left:18px" width="28" height="42" viewBox="0 0 28 42"><path d="M24 3 L6 21 L24 39" fill="none" stroke="#fff" stroke-width="6" stroke-linecap="round" stroke-linejoin="round"/></svg>
  <div class="abs logos"><span>Xandro</span><span>Dunepack</span><span>Norvane</span><span>Tallowby</span></div>
  <svg class="abs arrow" style="left:886px" width="28" height="42" viewBox="0 0 28 42"><path d="M4 3 L22 21 L4 39" fill="none" stroke="#fff" stroke-width="6" stroke-linecap="round" stroke-linejoin="round"/></svg>
</section>

<footer class="abs footer">
  <p class="abs footer-links">Home&nbsp; / &nbsp;Register&nbsp; / &nbsp;Events&nbsp; / &nbsp;Get Involved&nbsp; / &nbsp;Photos&nbsp; / &nbsp;Videos&nbsp; / &nbsp;Hall of Fame&nbsp; / &nbsp;Who We Are&nbsp; / &nbsp;Contact Us&nbsp; / &nbsp;Privacy</p>
  <p class="abs copy">Copyright ©2012 by <em>Grit &amp; Glory</em> | <span class="tc">T&amp;Cs</span></p>
  <div class="abs by">
    <h4>BROUGHT TO YOU BY</h4>
    <p class="partner">BrambleRoute.ie</p>
    <p class="tag">Get out, get Bramble Route!</p>
  </div>
</footer>
</body>
</html>
```